Climb Onward 2015

We're repeating the same promo in 2015 as a promo called Climb Onward for 2014. We simply need the look of the flyer changed for 2015. The concept is: we're better than the competition and we want to prove it. (without saying that) :)

Target Market(s)

This flyer will go to roofing contractors that do not use our company for their roofing needs. We would like them to try us and for that they get $500 off their order after buying $10K worth. We want an opportunity to prove to them that they will prefer us!

Industry/Entity Type

Promo

Colors
0356a4

Requirements
Must have
• Must not directly mention "competition"
Must be fairly reserved and male oriented (roofing contractors)
Title must be "Climb Onward in 2015"
Must have our logo & website www.marlowtinbuild.example
Must have Terms and Conditions (with Expiration of Dec 31, 2016)
Nice to have
• A design that POPS!
Feel free to add things that you think will work
Be creative

```html
<!DOCTYPE html>
<html lang="en">
<head>
<meta charset="utf-8">
<title>Climb Onward in 2015</title>
<link rel="stylesheet" href="https://fonts.googleapis.com/css2?family=Arimo:wght@400;700&display=swap">
<style>
  :root {
    --orange: #e8502a;
    --sky-hot: #fff1d6;
    --sky-mid: #f6a56e;
    --sky-deep: #e2683c;
    --charcoal: #1f1f1f;
    --charcoal-mid: #2c2c2c;
    --brand-blue: #0356a4;
    --white: #ffffff;
    --ink: #111111;
    --page: #e6e6e6;
  }
  * { box-sizing: border-box; margin: 0; padding: 0; }
  html, body { width: 1200px; height: 797px; overflow: hidden; }
  body {
    background: var(--page);
    font-family: "Arimo", Arial, sans-serif;
    display: flex; align-items: center; justify-content: center;
  }
  .flyer {
    width: 520px; height: 775px;
    background: var(--white);
    box-shadow: 0 6px 18px rgba(0,0,0,.18);
    display: flex; flex-direction: column;
    overflow: hidden;
  }
  .hero { position: relative; height: 270px; flex: none; }
  .hero-photo {
    position: absolute; inset: 0;
    background: radial-gradient(ellipse at 45% 45%, var(--sky-hot) 0%, var(--sky-mid) 30%, var(--sky-deep) 100%);
  }
  .hero-cap { position: absolute; top: 0; left: 0; }
  .hero-title {
    position: absolute; top: 26px; left: 0; right: 0;
    text-align: center; color: var(--white);
    font-weight: 700; font-size: 36px; letter-spacing: -.5px;
  }
  .offer-line {
    padding: 8px 22px 4px;
    font-weight: 700; font-size: 31px; color: var(--charcoal);
  }
  .offer-line .amount { color: var(--orange); }
  .offer-sub {
    border-top: 2px solid var(--charcoal);
    padding: 6px 22px 8px;
    font-weight: 700; font-size: 13.5px; line-height: 1.3; color: var(--ink);
    text-align: center;
  }
  .difference {
    background: repeating-linear-gradient(45deg, var(--charcoal) 0 3px, var(--charcoal-mid) 3px 6px);
    color: var(--white);
    padding: 12px 26px 12px;
    flex: none;
  }
  .difference h2 { font-size: 22px; font-weight: 700; margin-bottom: 5px; }
  .difference ul { list-style: none; font-size: 12.5px; line-height: 1.4; }
  .difference li::before { content: "- "; }
  .promo-copy {
    flex: 1;
    padding: 8px 30px;
    font-size: 14px; line-height: 1.35; color: var(--ink);
    text-align: center;
    display: flex; align-items: center; justify-content: center;
  }
  .brand-row {
    display: flex; align-items: center; justify-content: space-between;
    padding: 6px 22px 8px;
    flex: none;
  }
  .brand { display: flex; align-items: center; gap: 8px; }
  .brand-mark { width: 14px; height: 14px; background: var(--brand-blue); }
  .brand-name { font-weight: 700; font-size: 16px; color: var(--brand-blue); }
  .brand-web { font-weight: 700; font-size: 13px; color: var(--charcoal); }
  .terms {
    background: var(--orange);
    color: var(--white);
    font-size: 8.5px; line-height: 1.35;
    padding: 10px 20px 12px;
    flex: none;
  }
</style>
</head>
<body>
  <main class="flyer">
    <section class="hero">
      <div class="hero-photo" role="img" aria-label="Photo: silhouette of a man leaping between two rock ledges against an orange sunset sky"></div>
      <svg class="hero-cap" width="520" height="270" viewBox="0 0 520 270" aria-hidden="true">
        <path d="M0 0 H520 V140 Q400 40 250 62 Q100 86 0 200 Z" fill="var(--orange)"/>
      </svg>
      <h1 class="hero-title">Climb Onward in 2015</h1>
    </section>

    <section class="offer">
      <p class="offer-line">Receive a <span class="amount">$500.00 Voucher</span></p>
      <p class="offer-sub">After 40 Years of Servicing the Professional Contractor and Home Builder. We are Confident We Can Win You Over!</p>
    </section>

    <section class="difference">
      <h2>Discover the Marlowtin Difference</h2>
      <ul>
        <li>Triple Check System for Accurate Delivery</li>
        <li>Inventory of Major Brands</li>
        <li>Take Off Services</li>
        <li>New Fleet Monitored by Norlan</li>
        <li>Finance Options</li>
        <li>Marketing Programs to Increase Your Back Log</li>
        <li>Online Bill Pay</li>
      </ul>
    </section>

    <section class="promo-copy">
      <p>New customers who have purchased less than $2,000 in the past 6 months will be issued a $500 voucher, upon purchasing $10,000, to be used for additional purchases at Marlowtin Build Supply. One voucher per customer.</p>
    </section>

    <section class="brand-row">
      <div class="brand"><span class="brand-mark"></span><span class="brand-name">Marlowtin Build Supply</span></div>
      <span class="brand-web">www.marlowtinbuild.example</span>
    </section>

    <footer class="terms">
      <p>Terms and Conditions: Voucher is to be used for future purchases but may not be used to pay off any previous balance on current account. No one time purchasers. This promotion and your participation in it is void where prohibited by law, rules, or regulations. Marlowtin Build Supply reserves the right to cancel, suspend, limit and/or modify this promotion at any time for any reason, without notice. Expires December 31, 2016. All rights reserved by Marlowtin Build Supply.</p>
    </footer>
  </main>
</body>
</html>
```